TA BRAMLEY BUSINESS CARD DESIGN PROJECT

We need to utilize our logo that was expertly created on PixelHarbor and now need to match this with a business card design.

```html
<!DOCTYPE html>
<html lang="en">
<head>
<meta charset="utf-8">
<title>TA Bramley Business Card</title>
<link href="https://fonts.googleapis.com/css2?family=Montserrat:wght@400;500;700;800&display=swap" rel="stylesheet">
<style>
  :root {
    --brand-blue: #1158ad;
    --ink-black: #161616;
    --paper-white: #ffffff;
    --stage: #3a3a3a;
  }
  * { margin: 0; padding: 0; box-sizing: border-box; }
  html, body {
    width: 1200px; height: 900px; overflow: hidden;
    background: var(--stage);
    font-family: "Montserrat", sans-serif;
  }
  .canvas {
    position: relative; width: 1200px; height: 900px;
    display: flex; flex-direction: column; align-items: center; justify-content: center; gap: 50px;
  }
  .card {
    position: relative; width: 560px; height: 320px;
    border-radius: 22px; overflow: hidden;
  }
  .card-front {
    background: var(--brand-blue);
    display: flex; align-items: center; justify-content: center;
  }
  .brand-name {
    font-weight: 800; letter-spacing: 0.12em; white-space: nowrap;
  }
  .card-front .brand-name { color: var(--paper-white); font-size: 50px; }
  .card-back { background: var(--paper-white); }
  .card-back .wave { position: absolute; inset: 0; width: 100%; height: 100%; }
  .card-back .brand-name {
    position: absolute; top: 48px; right: 34px;
    color: var(--brand-blue); font-size: 30px;
  }
  .holder {
    position: absolute; top: 118px; left: 0;
    padding-left: 30px; border-left: 14px solid var(--brand-blue);
    margin-left: 20px;
  }
  .holder-name { color: var(--brand-blue); font-weight: 800; font-size: 21px; letter-spacing: 0.02em; }
  .holder-title { color: var(--ink-black); font-weight: 500; font-size: 15px; margin-top: 2px; }
  .contact {
    position: absolute; left: 64px; bottom: 26px;
    color: var(--paper-white); font-size: 13px; line-height: 1.45;
  }
  .contact-address { margin-bottom: 8px; }
  .contact-line { display: flex; align-items: center; gap: 8px; }
  .contact-line svg { width: 12px; height: 12px; fill: var(--brand-blue); flex: none; }
</style>
</head>
<body>
<main class="canvas">
  <section class="card card-front">
    <span class="brand-name">TA BRAMLEY</span>
  </section>

  <section class="card card-back">
    <svg class="wave" viewBox="0 0 560 320" preserveAspectRatio="none" aria-hidden="true">
      <path d="M0 215 C150 140 300 160 420 145 C500 135 540 120 560 102 L560 320 L0 320 Z" fill="var(--ink-black)"/>
      <path d="M95 192 C200 140 340 140 430 126 C505 114 540 98 560 82 L560 98 C540 116 500 134 420 142 C300 156 180 140 95 192 Z" fill="var(--brand-blue)"/>
    </svg>
    <span class="brand-name">TA BRAMLEY</span>
    <div class="holder">
      <div class="holder-name">DANIEL WREN</div>
      <div class="holder-title">Managing Director</div>
    </div>
    <div class="contact">
      <div class="contact-address">Your address, City<br>State, Zip 1234</div>
      <div class="contact-line">
        <svg viewBox="0 0 24 24"><path d="M6.6 10.8a15 15 0 0 0 6.6 6.6l2.2-2.2a1 1 0 0 1 1-.25 11.4 11.4 0 0 0 3.6.57 1 1 0 0 1 1 1V20a1 1 0 0 1-1 1A17 17 0 0 1 3 4a1 1 0 0 1 1-1h3.5a1 1 0 0 1 1 1c0 1.25.2 2.45.57 3.57a1 1 0 0 1-.25 1z"/></svg>
        <span>123 456 789</span>
      </div>
      <div class="contact-line">
        <svg viewBox="0 0 24 24"><path d="M2 5h20v14H2z M2 5l10 8 10-8" /></svg>
        <span>info@yourgmail.com</span>
      </div>
      <div class="contact-line">
        <svg viewBox="0 0 24 24"><circle cx="12" cy="12" r="10"/></svg>
        <span>www.yourwebsite.com</span>
      </div>
    </div>
  </section>
</main>
</body>
</html>
```